Kovát Lillas Physiotherapy Business Card Vienna

We need a business card design for a newly created Physiotherapy company based in Vienna Austria.
We seek a simple, modern, minimalist design without too much color variation. The font should look young/fresh, but definitely not childish or so. Since we are a starting Business, we currently haven't got a logo, if you feel like a logo would fit your design, feel free to use one, but it's not necessary.
Target Market(s)
Healthcare, young and elderly people with mobility issues
Industry/Entity Type
Health And Wellness
Contact Information for Business Card
Name: Lilla Kovát
Title description: Physiotherapist
Phone num: +43 664 2951 4086
e-mail: lilla.praxis@bluemail.example
Colors
Designer to choose colors to be used in the design.
Requirements
Must have
- Final design language must be in German, basically, the Title Description needs to be "Physiotherapeutin" the other details remain as in the English Language.
Nice to have
- Simple, modern, minimalist design
Should not have
- too many colors, Obvious use of a skeleton, skull, spline

```html
<!DOCTYPE html>
<html lang="de">
<head>
<meta charset="utf-8">
<title>Kovát Lillas Physiotherapy – Visitenkarte</title>
<link href="https://fonts.googleapis.com/css2?family=Jost:wght@400;500;600&display=swap" rel="stylesheet">
<style>
  :root {
    --backdrop: #dddddd;
    --card-light: #ffffff;
    --card-dark: #404042;
    --ink: #3a3a3c;
    --ink-inverse: #ffffff;
  }
  * { margin: 0; padding: 0; box-sizing: border-box; }
  html, body {
    width: 1200px;
    height: 897px;
    overflow: hidden;
    background: var(--backdrop);
    font-family: "Jost", sans-serif;
    color: var(--ink);
  }
  .card {
    position: absolute;
    left: 329px;
    width: 543px;
    height: 310px;
    overflow: hidden;
  }
  .card--front { top: 108px; background: var(--card-light); }
  .card--back { top: 479px; background: var(--card-dark); }

  .contact {
    position: absolute;
    left: 37px;
    top: 96px;
  }
  .contact__name {
    font-size: 22px;
    font-weight: 500;
    letter-spacing: 0.2em;
    line-height: 1;
    text-transform: uppercase;
    white-space: nowrap;
  }
  .contact__title {
    margin-top: 8px;
    font-size: 14px;
    font-weight: 400;
    line-height: 1;
  }
  .contact__rule {
    width: 15px;
    height: 1px;
    background: var(--ink);
    margin: 13px 0 14px;
  }
  .contact__line {
    font-size: 14px;
    line-height: 26px;
    white-space: nowrap;
  }

  .wordmark-vertical {
    position: absolute;
    right: 38px;
    bottom: 35px;
    writing-mode: vertical-rl;
    transform: rotate(180deg);
    display: flex;
    flex-direction: column;
    align-items: flex-start;
    gap: 6px;
    white-space: nowrap;
  }
  .wordmark-vertical__name {
    font-size: 34px;
    font-weight: 600;
    line-height: 1;
    text-transform: uppercase;
  }
  .wordmark-vertical__sub {
    font-size: 15px;
    font-weight: 400;
    letter-spacing: 0.52em;
    line-height: 1;
    text-transform: uppercase;
  }

  .wordmark {
    position: absolute;
    inset: 0;
    display: flex;
    flex-direction: column;
    align-items: center;
    justify-content: center;
    color: var(--ink-inverse);
    text-transform: uppercase;
    padding-top: 6px;
    white-space: nowrap;
  }
  .wordmark__name {
    font-size: 42px;
    font-weight: 600;
    line-height: 1;
  }
  .wordmark__sub {
    margin-top: 6px;
    font-size: 19px;
    font-weight: 400;
    letter-spacing: 0.46em;
    margin-right: -0.46em;
    line-height: 1;
  }
</style>
</head>
<body>
  <section class="card card--front">
    <div class="contact">
      <p class="contact__name">Lilla Kovát</p>
      <p class="contact__title">Physiotherapeutin</p>
      <div class="contact__rule"></div>
      <p class="contact__line">+43 664 2951 4086</p>
      <p class="contact__line">lilla.praxis@bluemail.example</p>
    </div>
    <div class="wordmark-vertical">
      <span class="wordmark-vertical__name">Kovát Lillas</span>
      <span class="wordmark-vertical__sub">Physiotherapy</span>
    </div>
  </section>

  <section class="card card--back">
    <div class="wordmark">
      <span class="wordmark__name">Kovát Lillas</span>
      <span class="wordmark__sub">Physiotherapy</span>
    </div>
  </section>
</body>
</html>
```